Pinecrest Harbor Foundation Web Design

The design we need is for a WordPress blog that will be our content platform. We are a registered 501(c)3 non-profit that focuses on financially supporting the treatment of cancer patients that have been told they have no hope and there is nothing the conventional medical system can do for them. Through this wesbite we want to both rasie awareness about the treatment options plus, raise funds for treating patients. The two primary target audiences of the site are...

1. Terminally ill patients and their families to let them know that there is an option other then hospice and that we are hear to support that option.

2. People looking to help donate to a worthwhile cause that resonates with them.

The website is https://pinecrestharborfoundation.org/

See attached logo designs!!!

Target Market(s)

Cancer patients and their families

Industry/Entity Type

Foundation

Font styles to use
Sans Serif

Colors
ffffff
fbed22

Requirements
Must have
• I like this look of this site. It is clean, simple, helpful, soft. I like the flow of the pages.
• http://www.meadowsforcalm.org/
• I like the design and flow but NOT the color or boldness
• https://tvbn-youth.org/
• I like this style for a donation page.
• https://www.tumorstudyhub.org/we-are-tsh/join-the-cause/donations/one-time-donation
• with the addition of a Would you like your employer to match? button.
Nice to have
• White black and gold - but soft
• Even possibly grayscale like the site I like.

```html
<!DOCTYPE html>
<html lang="en">
<head>
<meta charset="utf-8">
<title>Pinecrest Harbor Foundation</title>
<link href="https://fonts.googleapis.com/css2?family=Cinzel:wght@600;700&family=Lato:wght@400;700&family=Maven+Pro:wght@400;500&display=swap" rel="stylesheet">
<style>
:root{
  --gold:#f0c653;
  --gold-deep:#e2b43c;
  --ink:#1d1d1f;
  --charcoal:#2f2f31;
  --navy:#16202c;
  --maroon:#1e0d12;
  --footer:#1b1e22;
  --white:#ffffff;
  --muted:#555;
  --line:#d8d8d8;
}
*{box-sizing:border-box;margin:0;padding:0}
html,body{width:1200px;height:3475px;overflow:hidden}
body{position:relative;background:var(--white);font-family:"Lato",Arial,sans-serif;color:var(--ink)}
h2,h3,h4{font-weight:400}
.abs{position:absolute}
.btn{position:absolute;display:flex;align-items:center;justify-content:center;font-family:"Maven Pro",Arial,sans-serif;font-size:21px;text-transform:uppercase;letter-spacing:.5px}
.btn-dark{background:var(--charcoal);color:var(--white)}
.btn-gold{background:var(--gold);color:var(--white)}

/* top bar */
.topbar{left:0;top:0;width:1200px;height:42px;background:var(--gold);color:var(--white);font-size:14px;display:flex;align-items:center;padding-left:79px;gap:26px}
.topbar span{display:flex;align-items:center;gap:8px}

/* hero */
.hero{left:0;top:42px;width:1200px;height:646px;overflow:hidden;background:linear-gradient(100deg,#5d5752 0%,#3a3736 35%,#262628 60%,#1c1c1e 100%)}
.hero-photo{position:absolute;left:0;top:0;width:760px;height:646px;background:radial-gradient(ellipse at 40% 45%,#c9b7a4 0%,#8c7d6f 35%,rgba(60,56,54,0) 75%)}
.hero svg{position:absolute;left:0;top:0}
.brand{left:79px;top:58px;width:190px;height:82px;display:flex;align-items:center;justify-content:center;text-align:center;color:var(--white);font-family:"Cinzel",serif;font-weight:700;font-size:18px;line-height:1.25}
.nav{right:60px;top:80px;display:flex;gap:42px;color:var(--white);font-family:"Maven Pro",Arial,sans-serif;font-size:20px;align-items:center}
.hero-text{position:absolute;left:565px;top:440px;width:480px;text-align:center;color:var(--white);font-family:"Maven Pro",Arial,sans-serif;font-size:27px;line-height:1.12}
.hero .btn{left:702px;top:553px;width:188px;height:56px;border:2px solid var(--white)}

/* about */
.about-title{left:79px;top:745px;font-family:"Cinzel",serif;font-weight:700;font-size:38px;color:var(--ink)}
.about-title em{font-style:normal;color:var(--gold)}
.about-copy{left:79px;top:810px;width:640px;font-size:15px;line-height:1.7;color:var(--muted)}
.about-photo{left:748px;top:751px;width:374px;height:275px;background:linear-gradient(180deg,#d9dde2 0%,#b8bcc2 45%,#3a3b40 75%,#2a2b2f 100%)}

/* donate */
.donate{left:0;top:1100px;width:1200px;height:645px;background:radial-gradient(ellipse at 50% 40%,#2b3a4d 0%,#162130 55%,#0c131c 100%)}
.donate-title{left:0;top:1158px;width:1200px;text-align:center;font-family:"Cinzel",serif;font-weight:700;font-size:36px;color:var(--gold)}
.cause{position:absolute;top:1240px;width:260px;text-align:center}
.cause-photo{width:222px;height:222px;margin:0 auto;border-radius:50%;border:3px solid rgba(255,255,255,.8);padding:7px;background-clip:content-box;box-shadow:0 0 0 1px rgba(255,255,255,.3)}
.cause h3{margin-top:34px;font-family:"Maven Pro",Arial,sans-serif;font-weight:400;font-size:21px;line-height:1.25;color:var(--gold)}
.cause p{margin-top:10px;font-size:14px;line-height:1.6;color:var(--white)}
.cause .btn{position:relative;margin:20px auto 0;width:170px;height:55px}

/* support */
.support-title{left:0;top:1803px;width:1200px;text-align:center;font-family:"Maven Pro",Arial,sans-serif;font-weight:400;font-size:37px;color:var(--ink)}
.support-title em{font-style:normal;color:var(--gold)}
.support-band{left:0;top:2127px;width:1200px;height:313px;background:linear-gradient(180deg,#2a1017 0%,var(--maroon) 100%)}
.support-photo{left:278px;top:1900px;width:644px;height:292px;background:var(--white);border:1px solid var(--line);padding:10px;box-shadow:0 4px 12px rgba(0,0,0,.15)}
.support-photo div{width:100%;height:100%;background:linear-gradient(100deg,#b7b2ae 0%,#d8c9bb 40%,#9b8b7c 70%,#c9c3bb 100%)}
.support-copy{left:190px;top:2235px;width:820px;text-align:center;color:var(--white);font-size:14.5px;line-height:1.78}
.dots{left:0;top:2372px;width:1200px;display:flex;justify-content:center;gap:6px}
.dots i{width:14px;height:14px;border-radius:50%;border:2px solid var(--gold)}
.dots i.on{background:var(--gold)}

/* faq & news */
.split{left:612px;top:2440px;width:4px;height:428px;background:#f0f0f0;box-shadow:0 0 8px rgba(0,0,0,.08)}
.sec-title{font-family:"Maven Pro",Arial,sans-serif;font-weight:400;font-size:37px;color:var(--gold);top:2490px}
.faq{left:79px;top:2556px;width:519px;border:1px solid var(--line)}
.faq-q{height:44px;display:flex;align-items:center;gap:14px;padding-left:16px;border-bottom:1px solid var(--line);font-family:"Maven Pro",Arial,sans-serif;font-size:20px;color:var(--ink)}
.faq-q.open{color:var(--gold)}
.faq-a{padding:10px 16px;font-size:11.5px;line-height:1.6;color:var(--muted);border-bottom:1px solid var(--line)}
.news{position:absolute;left:667px;width:460px;height:114px}
.news-photo{position:absolute;left:0;top:0;width:116px;height:111px}
.news h4{position:absolute;left:130px;top:-4px;font-family:"Maven Pro",Arial,sans-serif;font-weight:400;font-size:19px;color:var(--gold)}
.news .date{position:absolute;left:130px;top:24px;font-size:12px;font-style:italic;color:var(--ink);display:flex;gap:6px;align-items:center}
.news p{position:absolute;left:130px;top:44px;width:320px;font-size:14px;line-height:1.5;color:var(--muted)}
.news .more{position:absolute;left:130px;top:90px;font-size:14px;color:var(--gold);letter-spacing:.5px}
.news-rule{left:797px;top:2678px;width:330px;height:1px;background:var(--line)}

/* cta */
.cta{left:0;top:2868px;width:1200px;height:105px;background:var(--gold)}
.cta p{position:absolute;left:79px;top:28px;width:790px;color:var(--white);font-size:14.5px;line-height:1.7}
.cta .btn{left:915px;top:28px;width:209px;height:56px}

/* footer */
.footer{left:0;top:2973px;width:1200px;height:433px;background:radial-gradient(ellipse at 60% 40%,#2a3038 0%,var(--footer) 70%)}
.f-head{top:3030px;font-family:"Maven Pro",Arial,sans-serif;font-weight:400;font-size:23px;color:var(--white);text-transform:uppercase}
.field{position:absolute;left:79px;width:449px;height:40px;background:var(--white);font-size:13px;color:#777;padding:10px 12px}
.submit{left:79px;top:3323px;width:187px;height:51px}
.services{left:612px;top:3090px;list-style:none;color:var(--white);font-size:14.5px;line-height:31px}
.find{left:865px;top:3080px;width:300px;color:var(--white);font-size:15px}
.find-row{position:absolute;left:0;display:flex;gap:22px;align-items:flex-start;width:300px}
.find-row svg{flex:none;margin-top:2px}
.find .gold{color:var(--gold);text-transform:uppercase}
.social{left:876px;top:3302px;display:flex;gap:13px}
.social i{width:56px;height:56px;border-radius:50%;border:2px solid rgba(255,255,255,.6)}
.social i.on{background:var(--gold);border-color:var(--gold)}
.copyright{left:0;top:3406px;width:1200px;height:69px;background:#121417;color:var(--white);font-size:14px;display:flex;align-items:center;justify-content:center;border-top:1px solid #2b2e33}
</style>
</head>
<body>

<div class="abs topbar">
  <span><svg width="14" height="14" viewBox="0 0 14 14"><circle cx="7" cy="7" r="6" fill="none" stroke="#fff" stroke-width="1.5"/></svg>Lorem Ipsum is simply dummy.</span>
  <span><svg width="14" height="14" viewBox="0 0 24 24"><path d="M6.6 10.8a15 15 0 0 0 6.6 6.6l2.2-2.2c.3-.3.7-.4 1-.2 1.1.4 2.3.6 3.6.6.6 0 1 .4 1 1V20c0 .6-.4 1-1 1A17 17 0 0 1 3 4c0-.6.4-1 1-1h3.5c.6 0 1 .4 1 1 0 1.3.2 2.5.6 3.6.1.3 0 .7-.2 1z" fill="#fff"/></svg>123-555-0147</span>
</div>

<section class="abs hero">
  <div class="hero-photo" role="img" aria-label="Photo of a smiling older couple embracing"></div>
  <svg width="1200" height="646" viewBox="0 0 1200 646"><polygon points="876,282 399,646 1200,646 1200,534" fill="var(--gold)" opacity=".93"/></svg>
  <p class="hero-text">we focuses on financially supporting the treatment of cancer patients</p>
  <div class="btn btn-dark">Contact Us</div>
</section>
<div class="abs brand">Pinecrest Harbor<br>Foundation</div>
<nav class="abs nav">
  <span>Home</span><span>About</span><span>Donate</span><span>Support Hospitality</span><span>News</span><span>Contact</span>
  <svg width="24" height="24" viewBox="0 0 24 24"><circle cx="10" cy="10" r="7" fill="none" stroke="var(--gold)" stroke-width="2"/><line x1="15" y1="15" x2="22" y2="22" stroke="var(--gold)" stroke-width="2"/></svg>
</nav>

<h2 class="abs about-title">About <em>Pinecrest Harbor</em></h2>
<p class="abs about-copy">Lorem Ipsum is simply dummy text of the printing and typesetting industry. Lorem Ipsum has been the industry's standard dummy text ever since the 1500s, when an unknown printer took a galley of type and scrambled it to make a type specimen book. It has survived not only five centuries, but also the leap into electronic typesetting, remaining essentially unchanged. It was popularised in the 1960s.</p>
<div class="btn btn-dark" style="left:79px;top:971px;width:181px;height:53px">Read More</div>
<div class="abs about-photo" role="img" aria-label="Group photo of the foundation team standing outdoors in the snow"></div>

<section class="abs donate" role="img" aria-label="Dark blue background with a faint medical pattern"></section>
<h2 class="abs donate-title">Donate</h2>
<div class="cause" style="left:65px">
  <div class="cause-photo" style="background-color:#c9a08a" role="img" aria-label="Photo of a mother and child"></div>
  <h3>Lorem Ipsum simply<br>dummy typeing</h3>
  <p>Lorem Ipsum is simply dummy text<br>of the printing and typesetting.</p>
  <div class="btn btn-gold">Read More</div>
</div>
<div class="cause" style="left:333px">
  <div class="cause-photo" style="background-color:#8fa86c" role="img" aria-label="Photo of an older couple outdoors"></div>
  <h3>Lorem Ipsum simply<br>dummy typeing</h3>
  <p>Lorem Ipsum is simply dummy text<br>of the printing and typesetting.</p>
  <div class="btn btn-gold">Read More</div>
</div>
<div class="cause" style="left:616px">
  <div class="cause-photo" style="background-color:#b9c2c9" role="img" aria-label="Photo of a doctor talking with a patient"></div>
  <h3>Lorem Ipsum simply<br>dummy typeing</h3>
  <p>Lorem Ipsum is simply dummy text<br>of the printing and typesetting.</p>
  <div class="btn btn-gold">Read More</div>
</div>
<div class="cause" style="left:894px">
  <div class="cause-photo" style="background-color:#a8b0bb" role="img" aria-label="Photo of a nurse caring for a patient"></div>
  <h3>Lorem Ipsum simply<br>dummy typeing</h3>
  <p>Lorem Ipsum is simply dummy text<br>of the printing and typesetting.</p>
  <div class="btn btn-gold">Read More</div>
</div>

<h2 class="abs support-title">Support <em>Hospitality</em></h2>
<div class="abs support-band"></div>
<div class="abs support-photo"><div role="img" aria-label="Photo of a patient in a headscarf embracing a caregiver"></div></div>
<p class="abs support-copy">Lorem Ipsum is simply dummy text of the printing and typesetting industry. Lorem Ipsum has been the industry's standard dummy text ever since the 1500s, when an unknown printer took a galley of type and scrambled it to make a type specimen book. It has survived not only five centuries, but also the leap into electronic typesetting, remaining essentially unchanged. It was popularised in the 1960s.</p>
<div class="abs dots"><i></i><i class="on"></i><i></i><i></i></div>

<div class="abs split"></div>
<h2 class="abs sec-title" style="left:79px">Faq</h2>
<div class="abs faq">
  <div class="faq-q open"><svg width="18" height="18" viewBox="0 0 18 18"><rect x="1" y="7" width="16" height="4" fill="var(--gold)"/></svg>What do I need to bring with me to my first visit?</div>
  <div class="faq-a">Lorem Ipsum is simply dummy text of the printing and typesetting industry. Lorem Ipsum has been the industry's standard dummy text ever since the 1500s,it has survived not only five centuries, but also the leap into electronic typesetting, remaining essentially unchanged.</div>
  <div class="faq-q"><svg width="18" height="18" viewBox="0 0 18 18"><path d="M7 1h4v6h6v4h-6v6H7v-6H1V7h6z" fill="var(--ink)"/></svg>Lorem Ipsum is simply dummy printing?</div>
  <div class="faq-q"><svg width="18" height="18" viewBox="0 0 18 18"><path d="M7 1h4v6h6v4h-6v6H7v-6H1V7h6z" fill="var(--ink)"/></svg>Lorem Ipsum is simply dummy printing?</div>
  <div class="faq-q" style="border-bottom:0"><svg width="18" height="18" viewBox="0 0 18 18"><path d="M7 1h4v6h6v4h-6v6H7v-6H1V7h6z" fill="var(--ink)"/></svg>Lorem Ipsum is simply dummy printing?</div>
</div>

<h2 class="abs sec-title" style="left:667px">Latest News</h2>
<div class="news" style="top:2549px">
  <div class="news-photo" style="background:linear-gradient(135deg,#5b7a99,#b98d6e)" role="img" aria-label="Photo of a child at home"></div>
  <h4>Lorem Ipsum is simply dummy text</h4>
  <div class="date"><svg width="11" height="11" viewBox="0 0 11 11"><rect x="1" y="2" width="9" height="8" fill="none" stroke="var(--ink)"/></svg>10 JULY 2016</div>
  <p>Lorem Ipsum is simply dummy text of the printing and typesetting industry.......</p>
  <div class="more">READ MORE &nbsp;›</div>
</div>
<div class="abs news-rule"></div>
<div class="news" style="top:2706px">
  <div class="news-photo" style="background:linear-gradient(135deg,#c9b48e,#6f7f8f)" role="img" aria-label="Photo of a classroom with students"></div>
  <h4>Lorem Ipsum is simply dummy text</h4>
  <div class="date"><svg width="11" height="11" viewBox="0 0 11 11"><rect x="1" y="2" width="9" height="8" fill="none" stroke="var(--ink)"/></svg>10 JULY 2016</div>
  <p>Lorem Ipsum is simply dummy text of the printing and typesetting industry.......</p>
  <div class="more">READ MORE &nbsp;›</div>
</div>

<section class="abs cta">
  <p>Lorem Ipsum is simply dummy text of the printing and typesetting industry. Lorem Ipsum has been the industry's standard dummy text ever since the 1500s, when an unknown printer took a galley of type and scrambled.</p>
  <div class="btn btn-dark">Contact Us</div>
</section>

<footer class="abs footer"></footer>
<h3 class="abs f-head" style="left:79px">Quick Inquiry</h3>
<div class="field" style="top:3079px">Name*</div>
<div class="field" style="top:3126px">Email*</div>
<div class="field" style="top:3173px">Services*</div>
<div class="field" style="top:3220px;height:93px">Message*</div>
<div class="btn btn-gold submit">Submit</div>

<h3 class="abs f-head" style="left:612px">Our Services</h3>
<ul class="abs services"><li>Home</li><li>About</li><li>Donate</li><li>Support Hospitality</li><li>News</li><li>Contact us</li></ul>

<h3 class="abs f-head" style="left:873px">Find Us</h3>
<div class="abs find">
  <div class="find-row" style="top:0"><svg width="18" height="24" viewBox="0 0 18 24"><path d="M9 0a9 9 0 0 0-9 9c0 7 9 15 9 15s9-8 9-15a9 9 0 0 0-9-9zm0 12a3 3 0 1 1 0-6 3 3 0 0 1 0 6z" fill="var(--gold)"/></svg><div><div class="gold">Pinecrest Harbor</div><div style="line-height:1.6">Suite 12, 9 Harbor Row Lower<br>Eastfield E05 QK41</div></div></div>
  <div class="find-row" style="top:86px"><svg width="20" height="20" viewBox="0 0 24 24"><path d="M6.6 10.8a15 15 0 0 0 6.6 6.6l2.2-2.2c.3-.3.7-.4 1-.2 1.1.4 2.3.6 3.6.6.6 0 1 .4 1 1V20c0 .6-.4 1-1 1A17 17 0 0 1 3 4c0-.6.4-1 1-1h3.5c.6 0 1 .4 1 1 0 1.3.2 2.5.6 3.6.1.3 0 .7-.2 1z" fill="var(--gold)"/></svg>123-555-0147</div>
  <div class="find-row" style="top:132px"><svg width="20" height="20" viewBox="0 0 20 20"><rect x="1" y="6" width="18" height="12" rx="2" fill="var(--gold)"/><rect x="5" y="1" width="10" height="7" fill="none" stroke="var(--gold)" stroke-width="2"/></svg>123-555-0147</div>
  <div class="find-row" style="top:176px"><svg width="20" height="16" viewBox="0 0 20 16"><rect x="0" y="0" width="20" height="16" rx="2" fill="var(--gold)"/><path d="M1 2l9 7 9-7" fill="none" stroke="var(--footer)" stroke-width="1.5"/></svg>info@pinecrestharbor.org</div>
</div>
<div class="abs social"><i class="on"></i><i></i><i></i><i></i></div>

<div class="abs copyright">© PINECREST HARBOR - 2017. All Right Reserved</div>

</body>
</html>
```